SkyvornQ Business Cards and Stationary Design

Need a design for our business cards and stationary. I want to carry on the theme of the logo. I want the business cards to have a design on the back. I would like the business cards and the stationary to carry the same theme, design scheme, and branding

Target Market(s)

Airlines and Maintenance Facilities

Industry/Entity Type

Aviation

Contact Information for Business Card

Name
Position Title
Address: 4827 Trellis Hollow Road, Fort Pierce, Florida, 34951
Office Number
Mobile Number
Email
Website

Font styles to use
Serif
Sans Serif

Colors

Designer to choose colors to be used in the design.

```html
<!DOCTYPE html>
<html lang="en">
<head>
<meta charset="utf-8">
<title>SkyvornQ Business Cards</title>
<link href="https://fonts.googleapis.com/css2?family=PT+Sans:wght@400;700&display=swap" rel="stylesheet">
<style>
  :root {
    --bg-light: #e4e4e4;
    --bg-dark: #cdcdcd;
    --card-white: #ffffff;
    --card-edge: #b9b9b9;
    --navy-deep: #070d38;
    --navy-brand: #001761;
    --navy-text: #0b1a5c;
    --sky: #3fc3f2;
    --white: #ffffff;
  }
  * { margin: 0; padding: 0; box-sizing: border-box; }
  html, body { width: 1200px; height: 1146px; overflow: hidden; }
  body {
    background: linear-gradient(135deg, var(--bg-light), var(--bg-dark));
    font-family: "PT Sans", sans-serif;
    position: relative;
  }
  .card {
    position: absolute;
    width: 758px;
    height: 432px;
    border-radius: 44px;
    overflow: hidden;
  }
  .card-front {
    left: 297px; top: 88px;
    background: var(--card-white);
    border: 2px solid var(--card-edge);
  }
  .card-back {
    left: 92px; top: 556px;
    background: var(--navy-brand);
  }
  .brand {
    position: absolute;
    display: flex;
    flex-direction: column;
    align-items: center;
  }
  .brand-ring {
    border-radius: 50%;
    border-style: solid;
  }
  .brand-name {
    font-family: "PT Sans", sans-serif;
    font-weight: 700;
    letter-spacing: 0.12em;
    line-height: 1;
  }
  .card-front .brand { left: 22px; top: 126px; width: 362px; }
  .card-front .brand-ring { width: 118px; height: 118px; border-width: 8px; border-color: var(--navy-text); margin-bottom: 24px; }
  .card-front .brand-name { font-size: 43px; color: var(--navy-text); }

  .web-strip {
    position: absolute;
    left: 398px; top: 60px;
    width: 35px; height: 304px;
    background: var(--sky);
  }
  .web-strip span {
    position: absolute;
    left: 50%; top: 50%;
    transform: translate(-50%, -50%) rotate(-90deg);
    white-space: nowrap;
    font-size: 20px;
    letter-spacing: 0.2em;
    color: var(--navy-deep);
  }
  .contact-panel {
    position: absolute;
    left: 438px; top: 60px;
    width: 320px; height: 304px;
    background: var(--navy-deep);
    color: var(--white);
    padding: 38px 0 0 22px;
  }
  .person-name { font-size: 27px; font-weight: 700; letter-spacing: 0.02em; line-height: 1.1; }
  .person-title { font-size: 23px; letter-spacing: 0.02em; margin-bottom: 16px; }
  .contact-list { list-style: none; font-size: 17px; }
  .contact-list li { display: flex; align-items: flex-start; gap: 6px; line-height: 27px; }
  .contact-list li.address { margin-top: 16px; }
  .contact-list svg { width: 16px; height: 16px; margin-top: 6px; flex-shrink: 0; }

  .card-back .brand { left: 0; top: 108px; width: 100%; }
  .card-back .brand-ring { width: 140px; height: 140px; border-width: 9px; border-color: var(--white); margin-bottom: 28px; }
  .card-back .brand-name { font-size: 46px; color: var(--white); }
  .back-web {
    position: absolute;
    left: 0; top: 354px; width: 100%;
    text-align: center;
    color: var(--white);
    font-size: 24px;
    letter-spacing: 0.2em;
  }
</style>
</head>
<body>
  <section class="card card-front">
    <div class="brand">
      <div class="brand-ring"></div>
      <div class="brand-name">SKYVORNQ</div>
    </div>
    <div class="web-strip"><span>www.skyvornq.com</span></div>
    <div class="contact-panel">
      <div class="person-name">MARCUS ELLERY</div>
      <div class="person-title">PRESIDENT</div>
      <ul class="contact-list">
        <li>
          <svg viewBox="0 0 16 16" fill="none" stroke="currentColor" stroke-width="1.3"><circle cx="8" cy="8" r="7"/><path d="M5.5 4.5l1.3 1.6-.8 1c.6 1.2 1.5 2.1 2.7 2.7l1-.8 1.6 1.3-.8 1.2C7.8 11.3 4.7 8.2 4.5 5.3z" fill="currentColor" stroke="none"/></svg>
          012-345-6789
        </li>
        <li>
          <svg viewBox="0 0 16 16" fill="none" stroke="currentColor" stroke-width="1.3"><circle cx="8" cy="8" r="7"/><rect x="5.7" y="4" width="4.6" height="8" rx="0.8"/></svg>
          012-345-6789
        </li>
        <li>
          <svg viewBox="0 0 16 16" fill="none" stroke="currentColor" stroke-width="1.3"><circle cx="8" cy="8" r="7"/><rect x="4.3" y="5.5" width="7.4" height="5" rx="0.5"/><path d="M4.5 6l3.5 2.5L11.5 6"/></svg>
          info@skyvornq.com
        </li>
        <li class="address">
          <svg viewBox="0 0 16 16" fill="none" stroke="currentColor" stroke-width="1.3"><circle cx="8" cy="8" r="7"/><path d="M8 12.3S5.2 9.3 5.2 7.2a2.8 2.8 0 015.6 0c0 2.1-2.8 5.1-2.8 5.1z"/><circle cx="8" cy="7.2" r="0.9" fill="currentColor" stroke="none"/></svg>
          <span>123, Street Name, City Name<br>Zipcode-012345</span>
        </li>
      </ul>
    </div>
  </section>

  <section class="card card-back">
    <div class="brand">
      <div class="brand-ring"></div>
      <div class="brand-name">SKYVORNQ</div>
    </div>
    <div class="back-web">www.skyvornq.com</div>
  </section>
</body>
</html>
```